Dog grooming business card
This is a business card for m dog grooming business like it say above.
In the priorities box below I will have the text that I want on the card.

Industry/Entity Type

Business

Colors

Designer to choose colors to be used in the design.

Requirements
Must have
• My logo and the insurance stamp must be on the card.

Text it must have :

Professional grooming services
Email: lunabrisk@mailvale.net
Text or call 1 705 318 6052
TWF certified/member
Pet first aid certified
Next appointment ___________________________________
Nice to have
• Greens to match my logo

```html
<!DOCTYPE html>
<html lang="en">
<head>
<meta charset="utf-8">
<title>Luna Brisk – Business Card</title>
<link rel="stylesheet" href="https://fonts.googleapis.com/css2?family=Lobster&family=Arimo:wght@400;700&display=swap">
<style>
  :root {
    --bg: #6b6e75;
    --ink: #1b161a;
    --paper: #ffffff;
    --green: #8cc63f;
    --text: #111111;
    --rule: #333333;
    --badge: #3a7fd0;
  }
  * { margin: 0; padding: 0; box-sizing: border-box; }
  html, body { width: 1200px; height: 960px; overflow: hidden; }
  body {
    background: var(--bg);
    font-family: "Arimo", Arial, sans-serif;
    position: relative;
  }
  .card {
    position: absolute;
    top: 147px;
    width: 380px;
    height: 665px;
    background: var(--paper);
    overflow: hidden;
    box-shadow: 0 10px 30px rgba(0,0,0,0.35);
  }
  .card--front { left: 180px; }
  .card--back { left: 640px; }
  .card__art { position: absolute; inset: 0; width: 100%; height: 100%; }

  .brand {
    position: absolute;
    display: flex;
    align-items: center;
    gap: 12px;
    left: 0; right: 0;
    justify-content: center;
  }
  .brand__dot {
    width: 46px; height: 46px;
    border-radius: 50%;
    background: var(--green);
  }
  .brand__name {
    font-family: "Lobster", cursive;
    font-size: 46px;
    color: var(--green);
    line-height: 1;
  }
  .card--front .brand { top: 140px; }
  .card--back .brand { top: 560px; }

  .tagline {
    position: absolute;
    left: 22px;
    right: 22px;
    bottom: 28px;
    font-family: "Lobster", cursive;
    font-size: 26px;
    line-height: 1.2;
    white-space: nowrap;
    color: var(--text);
  }

  .credentials {
    position: absolute;
    top: 44px;
    right: 28px;
    text-align: right;
    font-weight: 700;
    font-size: 19px;
    line-height: 1.2;
    color: var(--text);
  }
  .appointment {
    position: absolute;
    top: 118px;
    left: 34px;
    right: 34px;
  }
  .appointment__label {
    color: var(--green);
    font-size: 17px;
  }
  .appointment__line {
    height: 1px;
    background: var(--rule);
    margin-top: 28px;
  }
  .appointment__line + .appointment__line { margin-top: 44px; }
  .contact {
    position: absolute;
    top: 262px;
    left: 34px;
    font-size: 15px;
    line-height: 1.5;
    color: var(--text);
  }
  .contact__accent { color: var(--green); }
  .insurance-stamp {
    position: absolute;
    top: 330px;
    left: 34px;
    width: 92px;
    height: 42px;
    border: 2px solid var(--badge);
    border-radius: 8px;
    background: #eaf2fb;
  }
</style>
</head>
<body>

  <section class="card card--front">
    <svg class="card__art" viewBox="0 0 380 665" aria-hidden="true">
      <rect width="380" height="665" fill="var(--ink)"/>
      <path d="M0,318 C140,300 220,420 270,500 C310,560 340,572 380,576 L380,665 L0,665 Z" fill="var(--green)"/>
      <path d="M0,332 C132,316 208,432 258,512 C298,574 336,586 380,590 L380,665 L0,665 Z" fill="var(--paper)"/>
    </svg>
    <div class="brand">
      <span class="brand__name">Luna Brisk</span>
      <span class="brand__dot"></span>
    </div>
    <p class="tagline">Professional grooming services</p>
  </section>

  <section class="card card--back">
    <svg class="card__art" viewBox="0 0 380 665" aria-hidden="true">
      <path d="M0,510 C110,510 170,430 240,410 C300,392 340,388 380,388 L380,665 L0,665 Z" fill="var(--green)"/>
      <path d="M0,522 C112,522 174,444 244,424 C302,406 342,402 380,402 L380,665 L0,665 Z" fill="var(--ink)"/>
    </svg>
    <div class="credentials">
      <p>Pet first aid certified</p>
      <p>TWF certified/member</p>
    </div>
    <div class="appointment">
      <p class="appointment__label">Next appointment</p>
      <div class="appointment__line"></div>
      <div class="appointment__line"></div>
    </div>
    <div class="contact">
      <p>lunabrisk@mailvale.net</p>
      <p><span class="contact__accent">Text</span> or <span class="contact__accent">call</span> 1 705 318 6052</p>
    </div>
    <div class="insurance-stamp" role="img" aria-label="Insurance stamp"></div>
    <div class="brand">
      <span class="brand__name">Luna Brisk</span>
      <span class="brand__dot"></span>
    </div>
  </section>

</body>
</html>
```